Redesign of Form/Document Navigation Page

I need a redesign of our document and navigation bar on the left. We want the same navigation bar layout/setup but want the buttons and typography to be simple and matching all over. The form needs to be aesthetically pleasing and fit within the page.

1st attachment is our Direct Deposit and the second is the form continued.

```html
<!DOCTYPE html>
<html lang="en">
<head>
<meta charset="utf-8">
<title>Employee Direct Deposit Enrollment Form</title>
<link href="https://fonts.googleapis.com/css2?family=Raleway:wght@400;500;600;700;800&display=swap" rel="stylesheet">
<style>
:root{
  --navy:#24226b;
  --navy-line:#1d1b5c;
  --active:#2b3f9f;
  --red:#e5181b;
  --gold:#f4c419;
  --ink:#1b1b1b;
  --muted:#3a3a3a;
  --field:#c9c9c9;
  --white:#ffffff;
}
*{margin:0;padding:0;box-sizing:border-box}
html,body{width:1200px;height:839px;overflow:hidden;background:var(--white);font-family:"Raleway",sans-serif;color:var(--ink)}
.page{position:relative;width:1200px;height:839px}
.sidebar{position:absolute;left:0;top:0;width:266px;height:798px;background:var(--navy)}
.brand{height:105px;display:flex;align-items:center;padding-left:36px;gap:14px}
.brand-mark{width:50px;height:50px;border-radius:50%;background:var(--gold);flex:none}
.brand-name{color:var(--gold);font-weight:700;font-size:15.5px;line-height:17px;text-transform:uppercase}
.nav{list-style:none}
.nav li{height:43.5px;display:flex;align-items:center;justify-content:space-between;padding:0 22px 0 57px;color:#e8e8f4;font-size:12.5px;border-bottom:1px solid var(--navy-line)}
.nav li.back{background:var(--red);color:var(--white);font-weight:700;font-size:12.5px}
.nav li.active{background:var(--active)}
.nav svg{width:22px;height:22px;fill:none;stroke:#fff;stroke-width:1.3}
.topbar{position:absolute;left:266px;top:0;width:934px;height:39px;background:var(--red);color:var(--white);font-size:12px;font-weight:700;display:flex;align-items:center;padding:0 0 0 23px}
.topbar .link{display:flex;align-items:center;gap:9px;margin-right:23px}
.topbar svg{width:12px;height:12px;fill:#fff}
.topbar .user{margin-left:auto;margin-right:48px;display:flex;align-items:center;gap:8px}
.footer{position:absolute;left:0;top:798px;width:1200px;height:41px;background:var(--red);color:#fff;font-size:10.5px}
.social{position:absolute;left:15px;top:7px;display:flex;gap:4px}
.social span{width:31px;height:30px;background:var(--white)}
.copy{position:absolute;right:63px;top:14px}
.code{position:absolute;right:20px;top:14px}
.abs{position:absolute}
.title{left:266px;width:934px;top:82px;text-align:center;font-size:19px;font-weight:700;letter-spacing:.1px}
.body-text{left:315px;width:838px;font-size:9.6px;line-height:18px;text-align:justify;color:var(--muted)}
.alert{color:var(--red);font-size:11.4px;font-weight:500}
.center{left:266px;width:934px;text-align:center}
.attach{text-decoration:underline}
.btn{left:687px;top:275px;width:93px;height:32px;background:var(--navy);color:#fff;font-size:13.5px;font-weight:500;display:flex;align-items:center;justify-content:center}
.section{left:313px;top:340px;font-size:15px;font-weight:700}
.note{font-size:11.4px;left:313px}
.notify{left:313px;top:411px;font-size:13.4px;font-weight:600}
.radio{display:flex;align-items:center;gap:9px;color:var(--red);font-size:11.4px;font-weight:500}
.radio i{width:15px;height:15px;border-radius:50%;border:1px solid #bdbdbd;display:block;position:relative}
.radio i.on::after{content:"";position:absolute;left:3px;top:3px;width:7px;height:7px;border-radius:50%;background:var(--gold)}
.label{font-size:11.8px;font-weight:600;color:#333}
.input{border:1px solid var(--field);border-radius:2px;height:28px;width:196px;background:#fff}
.amount{left:609px;top:625px;color:var(--red);font-size:11.4px;font-weight:700}
.amount-box{left:660px;top:621px;width:43px;height:27px;border:1px solid var(--field);border-radius:2px;font-size:10px;font-weight:600;display:flex;align-items:center;padding-left:7px}
.pct{left:711px;top:628px;color:var(--red);font-size:11px;font-weight:600}
.important{left:315px;top:660px;font-size:14px;font-weight:700}
.important span{font-weight:400;font-size:12.5px;color:#333}
</style>
</head>
<body>
<div class="page">
  <aside class="sidebar">
    <div class="brand">
      <span class="brand-mark"></span>
      <span class="brand-name">Sentinel Patrol<br>Services</span>
    </div>
    <ul class="nav">
      <li class="back">Back to Profile <svg viewBox="0 0 24 24" style="fill:#fff;stroke:none"><path d="M10 5 3 11l7 6v-4c5 0 8 1 11 5-1-6-4-10-11-10z"/></svg></li>
      <li class="active">Direct Deposit <svg viewBox="0 0 24 24"><rect x="3" y="3" width="18" height="7"/><path d="M7 10v10h7v-6h4v-4"/><path d="M9 14h3"/></svg></li>
      <li>Change W-4 <svg viewBox="0 0 24 24"><circle cx="12" cy="10" r="7"/><path d="M5 22c1-4 4-5 7-5s6 1 7 5"/></svg></li>
      <li>Labour Code <svg viewBox="0 0 24 24"><circle cx="11" cy="8" r="4.5"/><path d="M3 21c1-5 4-7 8-7s6 1 7 3M18 16v6M15 19h6"/></svg></li>
      <li>Personal Information <svg viewBox="0 0 24 24"><rect x="2" y="4" width="20" height="16"/><circle cx="8" cy="11" r="2.5"/><path d="M4 17c1-3 7-3 8 0M14 10h5M14 14h5"/></svg></li>
      <li>Appraisal and Review <svg viewBox="0 0 24 24"><rect x="3" y="3" width="15" height="19"/><path d="M6 9l2 2 3-3M6 15l2 2 3-3M13 10h3M13 16h3M21 6l-5 10"/></svg></li>
      <li>Write Up-Slip <svg viewBox="0 0 24 24"><path d="M2 11h20v10H2zM2 11l10 6 10-6"/><path d="M7 11V4h7l3 3v4"/></svg></li>
      <li>Employee Performance <svg viewBox="0 0 24 24"><rect x="3" y="3" width="18" height="14"/><path d="M6 14l4-4 3 3 5-6M8 22l4-5 4 5M12 1v2"/></svg></li>
    </ul>
  </aside>

  <header class="topbar">
    <span class="link"><svg viewBox="0 0 12 12"><path d="M6 1 0 6h2v5h3V8h2v3h3V6h2z"/></svg>HOME</span>
    <span class="link"><svg viewBox="0 0 12 12"><path d="M6 0a6 6 0 1 0 0 12A6 6 0 0 0 6 0zm0 3a3 3 0 1 1 0 6 3 3 0 0 1 0-6z"/></svg>HELP</span>
    <span class="user">MARA QUINN <svg viewBox="0 0 12 12" style="fill:none;stroke:#fff;stroke-width:1"><rect x="2" y="5.5" width="8" height="6"/><path d="M4 5.5V3.5a2 2 0 0 1 4 0v2"/></svg></span>
  </header>

  <main>
    <h1 class="abs title">EMPLOYEE DIRECT DEPOSIT ENROLLMENT FORM</h1>
    <p class="abs body-text" style="top:126px">To Enroll in direct Deposit, Simply Fill out this orm, Attach a voided check for each checing account - not a deposit slip, Nam libero tempore, cum soluta nobis est eligendi optio cumque nihil impedit quo minus id quod maxime placeat facere possimus, omnis voluptas assumenda est, omnis dolor repellendus. Temporibus autem quibusdam et aut officiis debitis aut rerum necessitatibus saepe eveniet ut et voluptates repudiandae sint et molestiae non recusandae. Itaque earum rerum hic tenetur a sapiente delectus,</p>
    <p class="abs alert center" style="top:193px">Employees must attach a voided checj or each of their accounts to help verity their account numbers and bank routing numbers.</p>
    <p class="abs alert center attach" style="top:232px">Attach A Voided Check OR Bank Deposit Forum forthe account</p>
    <div class="abs btn">Refresh</div>

    <h2 class="abs section">ACCOUNT INFORMATION</h2>
    <p class="abs alert note" style="top:366px">The Last item must be for the remaining amount owed to you. To distribute to more accounts. please complete another form.</p>
    <p class="abs note" style="top:388px;font-weight:500">Make Sure to indicate what kind of account, along with enrolling or declining.</p>
    <p class="abs notify">** NOTIFY PAROLL IMMEDIATELY IF YOU CLOSE OR CHANGE BANK ACCOUNT**</p>

    <div class="abs radio" style="left:314px;top:445px"><i class="on"></i>New Enrollment</div>
    <div class="abs radio" style="left:449px;top:445px"><i></i>Change Enrollment</div>
    <div class="abs radio" style="left:585px;top:445px"><i></i>Cancel Enrollment</div>

    <span class="abs label" style="left:321px;top:483px">Bank Name</span>
    <span class="abs label" style="left:539px;top:483px">City</span>
    <span class="abs label" style="left:757px;top:483px">State</span>
    <div class="abs input" style="left:319px;top:508px"></div>
    <div class="abs input" style="left:537px;top:508px"></div>
    <div class="abs input" style="left:755px;top:508px"></div>

    <span class="abs label" style="left:321px;top:552px">Routing Transit#</span>
    <span class="abs label" style="left:539px;top:552px">Account Number</span>
    <div class="abs input" style="left:319px;top:576px"></div>
    <div class="abs input" style="left:537px;top:576px"></div>

    <div class="abs radio" style="left:314px;top:626px"><i></i>Checking</div>
    <div class="abs radio" style="left:449px;top:626px"><i></i>Savings</div>
    <span class="abs amount">Amount :</span>
    <div class="abs amount-box">100</div>
    <span class="abs pct">%</span>

    <p class="abs important">IMPORTANT ! <span>Please read and sign before completing and submitting</span></p>
    <p class="abs body-text" style="top:685px">Nam libero tempore, cum soluta nobis est eligendi optio cumque nihil impedit quo minus id quod maxime placeat facere possimus, omnis voluptas assumenda est, omnis dolor repellendus. Temporibus autem quibusdam et aut officiis debitis aut rerum necessitatibus saepe eveniet ut et voluptates repudiandae sint et molestiae non recusandae. Itaque earum rerum hic tenetur a sapiente delectus.</p>
  </main>

  <footer class="footer">
    <div class="social"><span></span><span></span><span></span></div>
    <span class="copy">© 2016. www.sentinelpatrol.com</span>
    <span class="code">M1</span>
  </footer>
</div>
</body>
</html>
```